New menu rebranding for Asian fusion

I have my current menu attached, but I want to change it and make it more attractive. The restaurant is an Asian Fusion. Food from Thailand, China, Japan, Indonesia, Malaysia, Cambodia. We cater to mid to high end consumers with an educated and sophisticated pallet. Maybe try a modern twist, or an authentic variation, maybe a mix. Please don't play with the logo too much, but feel free to play with the pattern. I also want to have as many pictures of dishes visible as possible. Additionally, keep in mind that the menu will be in two languages, so please design accordingly. Feel free to play around with the format of the menu and the logo too if you get carried away. Keep it in mind that this is also a take out menu too. Please check out the Instagram account lotus_crate As well as facebook etc. Let me know if you need any additional files. Thx and appreciated.
Updates

I have made an update to the Menu. It's not the original file. It's smaller now. Please see the attached PDF file. Best regards, Added Monday, February 02, 2015

Target Market(s)

Mid to high end

Industry/Entity Type

Restaurant

Number of Pages Required

3 page

Requirements
Must have
• dual language friendly. At least make space for it.
• Must keep logo.
Nice to have
• Would be nice to stick to same theme, not too much change to branding.

```html
<!DOCTYPE html>
<html lang="en">
<head>
<meta charset="utf-8">
<title>Lotus Crate Menu</title>
<link href="https://fonts.googleapis.com/css2?family=Michroma&display=swap" rel="stylesheet">
<style>
:root{
  --orange:#f7941d;
  --orange-deep:#ee5f24;
  --ink:#111;
  --white:#fff;
  --page:#fff;
  --pattern:#1a1208;
}
*{margin:0;padding:0;box-sizing:border-box}
html,body{width:1200px;height:1000px;overflow:hidden;background:var(--page)}
body{position:relative;font-family:"Michroma",sans-serif;color:var(--ink)}
.sheet{position:absolute;border:1px solid #555}
.cover{left:16px;top:10px;width:952px;height:476px;overflow:hidden}
.cover-panel{position:absolute;top:0;width:476px;height:476px;background:radial-gradient(ellipse at 50% 40%,var(--orange-deep) 0%,var(--orange) 62%)}
.cover-panel.front{left:0}
.cover-panel.back{left:476px;border-left:1px solid #f9b66a}
.brand{position:absolute;top:176px;left:0;width:100%;text-align:center;font-size:21px;letter-spacing:1px;line-height:1;color:var(--ink)}
.tagline{position:absolute;top:203px;left:0;width:100%;text-align:center;font-size:13px;line-height:1.2;color:var(--ink)}
.contacts{position:absolute;top:292px;left:0;width:100%;display:flex;justify-content:center;gap:18px;font-size:10px;line-height:15px;color:var(--white)}
.contact{display:flex;align-items:center;gap:7px}
.contact svg{width:15px;height:15px}
.website{position:absolute;top:313px;left:0;width:100%;text-align:center;font-size:11px;color:var(--ink)}
.pattern{position:absolute;background:var(--pattern)}
.cover .pattern{left:0;top:346px;width:952px;height:130px}
.menu{left:232px;top:507px;width:951px;height:476px;overflow:hidden}
.menu-list{position:absolute;left:0;top:0;width:475px;height:476px;background:radial-gradient(ellipse at 50% 45%,var(--orange-deep) 0%,var(--orange) 62%)}
.menu .pattern.top{left:0;top:6px;width:475px;height:30px}
.menu .pattern.bottom{left:0;top:438px;width:475px;height:26px}
.bar{position:absolute;top:51px;height:25px;background:var(--ink);color:var(--white);display:flex;align-items:center}
.bar .no{font-size:7px;margin-left:18px;width:40px}
.bar .title{font-size:11px;flex:1;text-align:center;padding-right:58px}
.bar.section{left:0;width:213px}
.bar.lang{left:261px;width:214px}
.price-head{position:absolute;left:228px;top:58px;font-size:9px;color:var(--white)}
.item{position:absolute;left:16px;width:440px;display:grid;grid-template-columns:28px 170px 44px}
.item .code{font-size:8px;padding-top:3px}
.item .name{font-size:10.5px;line-height:14px;color:var(--ink)}
.item .desc{grid-column:2;font-size:7.6px;letter-spacing:.2px;line-height:11px;color:var(--white)}
.item .price{grid-column:3;grid-row:1;font-size:8px;padding-top:3px;padding-left:16px}
.hero{position:absolute;left:475px;top:0;width:476px;height:476px;background:radial-gradient(ellipse at 50% 65%,#d9c777 0%,#c9b765 35%,#e9ece8 75%,#f6f6f6 100%)}
.tag{position:absolute;background:var(--ink);text-align:center;line-height:1.25}
.tag .dish{color:var(--white)}
.tag .alt{color:var(--orange)}
.tag.main{left:810px;top:51px;width:141px;height:42px;padding-top:5px;font-size:11px}
.thumb{position:absolute;top:312px;width:124px;height:122px;border:2px solid var(--orange)}
.thumb.dendeng{left:494px;background:radial-gradient(circle at 50% 50%,#6a1a1c,#3d0f12)}
.thumb.calamari{left:626px;background:radial-gradient(circle at 55% 45%,#e0a85a,#c9c5c2 70%)}
.tag.small{top:434px;width:124px;height:22px;font-size:7.5px;padding-top:2px}
.tag.small.dendeng{left:494px}
.tag.small.calamari{left:626px}
</style>
</head>
<body>

<section class="sheet cover" aria-label="Menu cover">
  <div class="cover-panel front">
    <div class="brand">LOTUS CRATE</div>
    <div class="tagline">fresh from the wok</div>
    <div class="contacts">
      <span class="contact"><svg viewBox="0 0 16 16"><circle cx="8" cy="8" r="7" fill="none" stroke="#fff" stroke-width="1.3"/><path d="M5.3 4.5l1.4 1.6-0.7 1.1c.6 1.2 1.5 2.1 2.6 2.6l1.1-.7 1.6 1.4-.8 1.2c-2.8-.4-5.2-2.8-5.6-5.6z" fill="#fff"/></svg>012 5550148</span>
      <span class="contact"><svg viewBox="0 0 16 16"><circle cx="8" cy="8" r="7.5" fill="#fff"/></svg>0550001234</span>
    </div>
    <div class="website">www.lotuscrate.co</div>
  </div>
  <div class="cover-panel back">
    <div class="brand">LOTUS CRATE</div>
    <div class="tagline">fresh from the wok</div>
    <div class="contacts">
      <span class="contact"><svg viewBox="0 0 16 16"><circle cx="8" cy="8" r="7" fill="none" stroke="#fff" stroke-width="1.3"/><path d="M5.3 4.5l1.4 1.6-0.7 1.1c.6 1.2 1.5 2.1 2.6 2.6l1.1-.7 1.6 1.4-.8 1.2c-2.8-.4-5.2-2.8-5.6-5.6z" fill="#fff"/></svg>012 5550148</span>
      <span class="contact"><svg viewBox="0 0 16 16"><circle cx="8" cy="8" r="7.5" fill="#fff"/></svg>0550001234</span>
    </div>
    <div class="website">www.lotuscrate.co</div>
  </div>
  <div class="pattern" role="img" aria-label="Repeating brand pattern band"></div>
</section>

<section class="sheet menu" aria-label="Appetizers spread">
  <div class="menu-list">
    <div class="pattern top" role="img" aria-label="Repeating brand pattern band"></div>
    <div class="bar section"><span class="no">No.</span><span class="title">Appetizers</span></div>
    <div class="price-head">SR</div>
    <div class="bar lang"><span class="no">No.</span><span class="title">Arrabic</span></div>

    <div class="item" style="top:104px"><span class="code">101</span><span class="name">Chicken Satay</span><span class="price">25</span><span class="desc">Bar BQ chicken skewers marinated in thai herbs served with sweet tangy peanut sauce</span></div>
    <div class="item" style="top:169px"><span class="code">102</span><span class="name">Shrimp Satay</span><span class="price">30</span><span class="desc">Bar BQ shrimp skewers marinated in thai herbs served with sweet tangy peanut sauce</span></div>
    <div class="item" style="top:234px"><span class="code">103</span><span class="name">Dendeng</span><span class="price">38</span><span class="desc">Our signature appetizer, crispy beef tossed in an aromatic spicy sauce with fried onions</span></div>
    <div class="item" style="top:307px"><span class="code">104</span><span class="name">Calamari</span><span class="price">28</span><span class="desc">Tender calamari lightly dusted and wok fried served with a chili soy dipping sauce</span></div>
    <div class="item" style="top:370px"><span class="code">105</span><span class="name">Spring Rolls</span><span class="price">23</span><span class="desc">Crispy fried spring rolls filled with fresh vegetables served with a sweet chilli dipping sauce</span></div>

    <div class="pattern bottom" role="img" aria-label="Repeating brand pattern band"></div>
  </div>

  <div class="hero" role="img" aria-label="Photo of chicken satay skewers with peanut sauce and cucumber salad"></div>
  <div class="tag main"><div class="dish">Chicken Satay</div><div class="alt">Arabic</div></div>

  <div class="thumb dendeng" role="img" aria-label="Photo of dendeng crispy beef"></div>
  <div class="tag small dendeng"><div class="dish">Dendeng</div><div class="alt">Arabic</div></div>
  <div class="thumb calamari" role="img" aria-label="Photo of fried calamari rings with lime"></div>
  <div class="tag small calamari"><div class="dish">Calamari</div><div class="alt">Arabic</div></div>
</section>

</body>
</html>
```